Institutional website for an IT Consulting company

Web design + HTML + CSS / Bootstrap + JS (interaction) integration in order to extend our existing website brightvale.coop.
Our website is currently aiming only for recruitment and not for customers, we want to provide a fluid transition between customer side website (this project) and recruitment website (existing site).

Ideally we would love the new design to be "inspired" by our actual graphic chart (Colors mainly). It should provide a great user experience and a landing page (or any mean) allowing the visitor to easily switch from the end customer front end (this project), the recruitment front end (existing front end https://www.brightvale.coop/) and the existing member front end (an other existing front end dedicated to members already existing).

In attachment you will find the expected site content mainly a one page with a first level of information and "link" to sub pages (a way to directly access this sub pages should also be provided).

The website should be accessible on mobile device and desktop.

The attachment is in french as it reflect the final site content, but if google translate isn't sufficient to have a general idea of the content, feel free to ask. We would love to have some visual representation for some categories.

Target Market(s)

fortune 500 companies

Industry/Entity Type

It Company

Coding

Coded - Design and coding required

Number of Pages Required

5+ page

Requirements
Must have
• This project must have an easy way to navigate between 3 sub sites, the customer one (the one designed here), the consultant / recruitment one (the existing one at brightvale.coop), the members one.

A one page experience at first leading to detail pages.

Custom made visuals to illustrate each categories.

Inspiration websites : pirog[.]fr ; tasklynn[.]com ; dorvelo[.] com ...

Be inspired by the existing color from our logo and existing website at brightvale[.]coop

```html
<!DOCTYPE html>
<html lang="en">
<head>
<meta charset="utf-8">
<title>Contact Us – Brightvale.coop</title>
<link rel="stylesheet" href="https://fonts.googleapis.com/css2?family=Montserrat:wght@400;500;600;700&family=Open+Sans:ital,wght@0,400;0,600;1,400&display=swap">
<style>
:root{
  --teal:#13a9b6;
  --teal-dark:#0f9aa6;
  --ink:#0b3f3f;
  --text:#2b2b2b;
  --muted:#5d5d5d;
  --line:#cfcfcf;
  --white:#ffffff;
}
*{box-sizing:border-box;margin:0;padding:0}
html,body{width:1200px;height:2434px;overflow:hidden;background:var(--white)}
body{position:relative;font-family:"Open Sans",sans-serif;color:var(--text)}
.abs{position:absolute}
.brand{font-family:"Montserrat",sans-serif;font-weight:700;color:var(--ink);letter-spacing:1px;display:flex;align-items:center;gap:10px}
.brand .mark{width:22px;height:22px;background:var(--teal)}
.header-brand{left:110px;top:42px;font-size:30px}
.top-links{right:112px;top:16px;font-family:"Montserrat",sans-serif;font-size:15px;font-weight:500;color:var(--ink);display:flex;gap:12px;align-items:center}
.top-links svg{vertical-align:-2px;margin-right:5px}
.nav{right:112px;top:49px;display:flex;gap:17px}
.nav a{display:block;height:49px;line-height:45px;padding:0 14px;border:2px solid #9a9a9a;font-family:"Montserrat",sans-serif;font-weight:600;font-size:15px;color:#555;text-decoration:none}
.nav a.active{background:#2b2b2b;border-color:#2b2b2b;color:#fff}
.hero{left:0;top:121px;width:1200px;height:405px;background:linear-gradient(90deg,#e9e6df 0%,#d8d4ca 40%,#5a6a80 70%,#2b3f5e 100%)}
.hero h1{position:absolute;left:112px;top:162px;font-family:"Montserrat",sans-serif;font-weight:700;font-size:68px;color:#222;letter-spacing:1px}
.dots{position:absolute;left:550px;top:345px;display:flex;gap:9px}
.dots i{width:18px;height:18px;border-radius:50%;border:2px solid #444;display:block}
.dots i.on{background:#555;border-color:#555}
.sec-title{font-family:"Montserrat",sans-serif;font-weight:500;font-size:24px;color:#222}
.field{border:1px solid #bdbdbd;border-radius:5px;font-size:15px;color:#555;padding:13px 15px}
.submit{left:603px;top:925px;width:111px;height:44px;background:var(--teal);color:#fff;font-family:"Montserrat",sans-serif;font-weight:700;font-size:16px;text-align:center;line-height:44px;letter-spacing:.5px}
.info-row{left:779px;display:flex;gap:16px;font-size:17px;color:#333;line-height:24px}
.ico{width:36px;height:36px;border:1px solid #bbb;border-radius:50%;display:flex;align-items:center;justify-content:center;flex:none}
.social{display:flex;gap:10px}
.social i{display:block;width:44px;height:44px;border:1px solid #999;border-radius:50%}
.map{left:112px;top:1037px;width:977px;height:397px;background:linear-gradient(135deg,#f1efe9,#e6e4df 50%,#f3ecdd)}
.band{left:0;top:1506px;width:1200px;height:511px;background:var(--teal)}
.band h2{position:absolute;left:0;width:1200px;top:50px;text-align:center;font-family:"Montserrat",sans-serif;font-weight:700;font-size:46px;color:#fff}
.client-box{position:absolute;left:110px;top:156px;width:240px;height:115px;border:9px solid #fff;display:flex;align-items:center;justify-content:center;gap:10px;font-family:"Montserrat",sans-serif;font-weight:700;font-size:30px;color:#fff;background:var(--teal-dark)}
.client-box span.sq{width:20px;height:20px;background:#fff}
.band p{position:absolute;left:383px;width:710px;font-family:"Montserrat",sans-serif;font-size:17px;line-height:31px;color:#fff}
.band .divider{position:absolute;left:110px;top:302px;width:977px;height:1px;background:rgba(255,255,255,.35)}
.avatar{position:absolute;left:108px;top:327px;width:120px;height:120px;border-radius:50%;background:linear-gradient(160deg,#e8e6e2,#b9a596);border:2px solid #fff}
.person{position:absolute;left:256px;top:362px;font-family:"Montserrat",sans-serif;font-size:19px;line-height:31px;color:#fff}
.quote{top:325px;font-style:italic;font-family:"Open Sans",sans-serif!important;font-size:17px!important;line-height:28px!important}
.arrows{position:absolute;left:1028px;top:428px;display:flex;gap:7px}
.arrows i{width:24px;height:24px;border-radius:50%;background:#fff;display:flex;align-items:center;justify-content:center}
.footer-brand{left:110px;top:2158px;font-size:30px}
.fcol{top:2068px}
.fcol h3{font-family:"Montserrat",sans-serif;font-weight:500;font-size:20px;color:#333;margin-bottom:10px}
.fcol li{list-style:none;font-size:15px;color:#666;line-height:26.6px}
.fcol .find{display:flex;gap:8px;line-height:27px}
.frule{left:110px;top:2347px;width:977px;height:2px;background:#ccc}
.copy{left:110px;top:2378px;font-size:16px;color:#666}
.fsocial{left:945px;top:2368px}
</style>
</head>
<body>
<header>
  <div class="abs brand header-brand"><span>BRIGHTVALE.COOP</span><span class="mark"></span></div>
  <div class="abs top-links">
    <span><svg width="13" height="13" viewBox="0 0 12 12"><path d="M1 11l1-3 6-6 2 2-6 6z" fill="#13a9b6"/></svg>REGISTER</span><span>|</span>
    <span><svg width="11" height="13" viewBox="0 0 10 12"><rect x="1" y="5" width="8" height="7" fill="#13a9b6"/><path d="M3 5V3a2 2 0 014 0v2" stroke="#13a9b6" stroke-width="1.5" fill="none"/></svg>LOG IN</span><span>|</span>
    <span><svg width="13" height="13" viewBox="0 0 12 12"><circle cx="6" cy="6" r="6" fill="#13a9b6"/><text x="6" y="9.5" font-size="9" text-anchor="middle" fill="#fff" font-family="Arial">?</text></svg>HELP</span>
  </div>
  <nav class="abs nav">
    <a href="#">I AM BRIGHTVALE</a>
    <a href="#">I WISH TO JOIN BRIGHTVALE</a>
    <a href="#" class="active">CONTACT US</a>
  </nav>
</header>

<section class="abs hero" role="img" aria-label="Photo of a businessman in a suit reading a tablet in a bright office">
  <h1>CONTACT US</h1>
  <div class="dots"><i class="on"></i><i></i><i></i><i></i></div>
</section>

<section class="contact">
  <h2 class="abs sec-title" style="left:110px;top:619px">CONTACT FORM</h2>
  <div class="abs field" style="left:112px;top:680px;width:296px;height:46px">Name :</div>
  <div class="abs field" style="left:418px;top:680px;width:296px;height:46px">Phone no :</div>
  <div class="abs field" style="left:112px;top:742px;width:602px;height:45px">Email :</div>
  <div class="abs field" style="left:112px;top:804px;width:602px;height:99px">Message :</div>
  <div class="abs submit">SUBMIT</div>

  <h2 class="abs sec-title" style="left:779px;top:620px">CONTACT INFORMATION</h2>
  <div class="abs info-row" style="top:676px">
    <span class="ico"><svg width="14" height="18" viewBox="0 0 14 18"><path d="M7 1a6 6 0 016 6c0 4-6 10-6 10S1 11 1 7a6 6 0 016-6z" fill="none" stroke="#13a9b6" stroke-width="1.6"/><circle cx="7" cy="7" r="2" fill="#13a9b6"/></svg></span>
    <span>COWORKLINK - BRIGHTVALE.COOP -<br>12 Rue des Tilleuls 75011 Paris</span>
  </div>
  <div class="abs info-row" style="top:747px;align-items:center">
    <span class="ico"><svg width="18" height="13" viewBox="0 0 18 13"><rect width="18" height="13" rx="1.5" fill="#13a9b6"/><path d="M1 1l8 6 8-6" stroke="#fff" stroke-width="1.3" fill="none"/></svg></span>
    <span>contact@brightvale.coop</span>
  </div>
  <div class="abs info-row" style="top:808px;align-items:center">
    <span class="ico"><svg width="16" height="16" viewBox="0 0 16 16"><path d="M3 1l3 3-2 2c1 2 3 4 5 5l2-2 3 3-2 3C7 15 1 9 1 3z" fill="#13a9b6"/></svg></span>
    <span>01 70 45 19 26</span>
  </div>
  <h2 class="abs sec-title" style="left:779px;top:877px">SOCIAL MEDIA</h2>
  <div class="abs social" style="left:779px;top:929px"><i></i><i></i><i></i></div>
</section>

<div class="abs map" role="img" aria-label="Street map of the office neighbourhood in Paris with a location marker"></div>

<section class="abs band">
  <h2>CLIENT TESTIMONIALS</h2>
  <div class="client-box"><span class="sq"></span><span>NORTHLINE</span></div>
  <p style="top:150px">Nemo enim ipsam voluptatem quia voluptas sit aspernatur aut odit aut fugit, sed quia csequ untur magni dolores eos qui ratione voluptatem sequi nesciunt. Neque porro quisquam est, qui dolorem ipsum quia dolor sit amet, consectetur, adipisci velit, sed quia non num eimodi tempora incidunt ut labore et dolore magnam aliquam..</p>
  <div class="divider"></div>
  <div class="avatar" role="img" aria-label="Portrait photo of the client"></div>
  <div class="person">John Doe<br>CEO</div>
  <p class="quote">“Nam libero tempore, cum soluta nobis est eligendi opticum que nihil impedit quo minus id quod maxime placeat facere possimus, omnis voluptas assumenda est, omnis dolor rep ellendu autem quibusdam et aut .”</p>
  <div class="arrows">
    <i><svg width="10" height="12" viewBox="0 0 10 12"><path d="M7 1L2 6l5 5" stroke="#13a9b6" stroke-width="2.5" fill="none"/></svg></i>
    <i><svg width="10" height="12" viewBox="0 0 10 12"><path d="M3 1l5 5-5 5" stroke="#13a9b6" stroke-width="2.5" fill="none"/></svg></i>
  </div>
</section>

<footer>
  <div class="abs brand footer-brand"><span>BRIGHTVALE.COOP</span><span class="mark"></span></div>
  <div class="abs fcol" style="left:468px">
    <h3>Information</h3>
    <ul><li>About us</li><li>Team</li><li>Jobs</li><li>Hurry</li><li>Freelancing news</li><li>Data protection</li><li>Help</li><li>Sitemap</li></ul>
  </div>
  <div class="abs fcol" style="left:673px">
    <h3>Quick Links</h3>
    <ul><li>Offers and prices</li><li>Company</li><li>Open Brightvale coop</li><li>Insights</li><li>Create my Profile</li></ul>
  </div>
  <div class="abs fcol" style="left:879px">
    <h3>Find Us</h3>
    <ul>
      <li class="find"><svg width="11" height="16" viewBox="0 0 14 18" style="margin-top:5px"><path d="M7 1a6 6 0 016 6c0 4-6 10-6 10S1 11 1 7a6 6 0 016-6z" fill="#13a9b6"/><circle cx="7" cy="7" r="2" fill="#fff"/></svg><span>24 Rue Verlaine<br>75008 Paris</span></li>
      <li class="find" style="margin-top:20px"><svg width="14" height="14" viewBox="0 0 16 16" style="margin-top:6px"><path d="M3 1l3 3-2 2c1 2 3 4 5 5l2-2 3 3-2 3C7 15 1 9 1 3z" fill="#13a9b6"/></svg><span>01 70 45 19 26</span></li>
      <li class="find" style="margin-top:28px"><svg width="17" height="12" viewBox="0 0 18 13" style="margin-top:8px"><rect width="18" height="13" rx="1.5" fill="#13a9b6"/><path d="M1 1l8 6 8-6" stroke="#fff" stroke-width="1.3" fill="none"/></svg><span>contact@brightvale.coop</span></li>
    </ul>
  </div>
  <div class="abs frule"></div>
  <div class="abs copy">© 2020, Brightvale.coop.</div>
  <div class="abs social fsocial"><i></i><i></i><i></i></div>
</footer>
</body>
</html>
```